Acupuncture business needs business card design

I need a business card for an acupuncture clinic called "Harbourlight Wellness"
It will need the following details:
My name: Marcus Pelling
Acupuncturist
Member TVBH
KWF Treatment Provider
Ph numbers: 581 2734 027 418 5620
Email: marcus@hbwel.example.nz
On the back it will need a table with 2 columns for appointments, one column for time and one for date.

Industry/Entity Type

Clinic

Contact Information for Business Card

Marcus Pelling
Acupuncturist
Member TVBH
KWF Treatment Provider
Email: marcus@hbwel.example.nz

Requirements
Must have
• Marcus Pelling
• Acupuncturist
• Member TVBH
• KWF Treatment Provider
• Ph numbers: 581 2734 027 418 5620
• Email: marcus@hbwel.example.nz
• On the back it will need a table with 2 columns for appointments, one column for time and one for date.

```html
<!DOCTYPE html>
<html lang="en">
<head>
<meta charset="utf-8">
<title>Harbourlight Wellness – Business Card</title>
<link rel="stylesheet" href="https://fonts.googleapis.com/css2?family=Questrial&display=swap">
<style>
  :root {
    --backdrop: #dccfa6;
    --card-dark: #0b0b0c;
    --card-light: #ffffff;
    --teal: #1b7f95;
    --teal-deep: #146a7e;
    --sky: #29a9dc;
    --field: #ffffff;
    --ink-light: #f2f6f8;
  }
  * { box-sizing: border-box; margin: 0; padding: 0; }
  html, body {
    width: 1200px; height: 978px; overflow: hidden;
    background: var(--backdrop);
    font-family: "Questrial", "Century Gothic", sans-serif;
  }
  .stage { position: relative; width: 1200px; height: 978px; }
  .card {
    position: absolute; left: 280px; width: 640px; height: 366px;
    border-radius: 26px; overflow: hidden;
    box-shadow: 0 10px 24px rgba(0,0,0,0.25);
  }
  .brand { position: absolute; display: flex; align-items: center; gap: 14px; }
  .brand-dot { width: 46px; height: 46px; border-radius: 50%; background: var(--sky); flex: none; }
  .brand-text { display: flex; flex-direction: column; }
  .brand-name { font-size: 36px; color: var(--sky); line-height: 1; white-space: nowrap; }
  .brand-tagline {
    font-size: 12px; letter-spacing: 5px; color: var(--sky); margin-top: 7px;
    text-transform: uppercase; white-space: nowrap;
  }
  /* Back of card */
  .card-back { top: 70px; background: var(--card-dark); color: var(--ink-light); }
  .card-back .brand { left: 50px; top: 38px; }
  .appointment {
    position: absolute; left: 60px; top: 140px; width: 520px;
    border-collapse: separate; border-spacing: 0 18px;
  }
  .appointment th {
    text-align: left; font-weight: normal; font-size: 22px; width: 70px; color: var(--ink-light);
  }
  .field-row { display: flex; gap: 8px; }
  .field { height: 34px; background: var(--field); flex: 1; }
  .field.short { flex: 0 0 58px; }
  .website {
    position: absolute; left: 0; right: 0; bottom: 36px; text-align: center;
    font-size: 22px; letter-spacing: 3px; color: var(--ink-light);
  }
  /* Front of card */
  .card-front { top: 540px; background: var(--card-light); }
  .front-band { position: absolute; inset: 0; width: 640px; height: 366px; }
  .card-front .brand { left: 130px; top: 40px; }
  .card-front .brand-name { color: var(--teal); }
  .card-front .brand-tagline { color: var(--teal); }
  .practitioner { position: absolute; left: 240px; top: 140px; width: 300px; text-align: center; }
  .practitioner-name { font-size: 20px; color: var(--teal-deep); font-weight: bold; }
  .practitioner-role { font-size: 14px; color: var(--sky); line-height: 1.35; margin-top: 4px; }
  .contact {
    position: absolute; left: 40px; top: 258px; color: var(--ink-light); font-size: 16px; line-height: 1.6;
  }
  .contact-line { display: flex; align-items: center; gap: 8px; white-space: nowrap; }
  .contact-line svg { width: 16px; height: 16px; flex: none; }
</style>
</head>
<body>
<main class="stage">

  <section class="card card-back" aria-label="Appointment card, back">
    <div class="brand">
      <span class="brand-dot"></span>
      <div class="brand-text">
        <span class="brand-name">Harbourlight Wellness</span>
        <span class="brand-tagline">Acupuncture Physiotherapy</span>
      </div>
    </div>
    <table class="appointment">
      <tr>
        <th scope="row">Time</th>
        <td><div class="field-row"><span class="field"></span></div></td>
      </tr>
      <tr>
        <th scope="row">Date</th>
        <td><div class="field-row"><span class="field"></span><span class="field short"></span><span class="field"></span></div></td>
      </tr>
    </table>
    <p class="website">www.hbwel.example.nz</p>
  </section>

  <section class="card card-front" aria-label="Business card, front">
    <svg class="front-band" viewBox="0 0 640 366" aria-hidden="true">
      <path d="M0 150 C 200 170, 420 300, 640 280 L640 366 L0 366 Z" fill="var(--sky)"/>
      <path d="M0 162 C 200 182, 420 312, 640 292 L640 366 L0 366 Z" fill="var(--card-light)"/>
      <path d="M0 170 C 200 190, 420 320, 640 300 L640 366 L0 366 Z" fill="var(--teal)"/>
    </svg>
    <div class="brand">
      <span class="brand-dot"></span>
      <div class="brand-text">
        <span class="brand-name">Harbourlight Wellness</span>
        <span class="brand-tagline">Acupuncture Physiotherapy</span>
      </div>
    </div>
    <div class="practitioner">
      <p class="practitioner-name">Marcus Pelling</p>
      <p class="practitioner-role">Acupuncturist Member TVBH<br>KWF Treatment Provider</p>
    </div>
    <div class="contact">
      <p class="contact-line">
        <svg viewBox="0 0 16 16" aria-hidden="true"><path d="M4 1.5h2.5l1 3.5-1.8 1.2a8 8 0 0 0 4 4l1.2-1.8 3.5 1V12a2.5 2.5 0 0 1-2.5 2.5A11.5 11.5 0 0 1 1.5 4 2.5 2.5 0 0 1 4 1.5z" fill="currentColor"/></svg>
        581-2734 · 027-418-5620
      </p>
      <p class="contact-line">
        <svg viewBox="0 0 16 16" aria-hidden="true"><rect x="1.5" y="3.5" width="13" height="9" rx="1" fill="none" stroke="currentColor" stroke-width="1.4"/><path d="M2 4l6 5 6-5" fill="none" stroke="currentColor" stroke-width="1.4"/></svg>
        marcus@hbwel.example.nz
      </p>
      <p class="contact-line">Street Name, City Name, Zipcode-01234</p>
    </div>
  </section>

</main>
</body>
</html>
```